Boutique custom software development company needs new business card

Our nearly 20 year old custom software development company would like to better include the fact that we are now providing Bitcoin services. These new services are B2B include education (how to acquire and securely hold Bitcoin) and integrating Bitcoin payments into existing ecommerce sites or other existing systems. Please keep the card clean and simple. Attached is our current design and some other files. vextorial.com

Target Market(s)

businesses owners interested in long term relationship

Industry/Entity Type

Custom software development and Bitcoin

Contact Information for Business Card

Dale Parker, dale@vextorial.com, vextorial.com, (888) 555-VXTRL

Font styles to use
Other font styles liked:
• monospace

Requirements
Must have
• double-sided
Nice to have
• clean and simple
Should not have
• physical address

```html
<!DOCTYPE html>
<html lang="en">
<head>
<meta charset="utf-8">
<title>Vextorial business card</title>
<link href="https://fonts.googleapis.com/css2?family=Lato:wght@400;700;900&family=Montserrat:wght@800&display=swap" rel="stylesheet">
<style>
  :root {
    --backdrop: #d9d9d9;
    --paper: #ffffff;
    --brand-blue: #2e6fc4;
    --brand-orange: #f57c17;
    --ink-grey: #555555;
  }
  * { box-sizing: border-box; margin: 0; padding: 0; }
  html, body { width: 1200px; height: 1056px; overflow: hidden; }
  body {
    background: var(--backdrop);
    font-family: "Lato", Arial, sans-serif;
    position: relative;
  }
  .card {
    position: absolute;
    left: 220px;
    width: 760px;
    height: 434px;
    box-shadow: 0 10px 28px rgba(0,0,0,0.18);
  }
  /* Front side */
  .card-front { top: 52px; background: var(--paper); }
  .brand-lockup { position: absolute; left: 48px; top: 140px; width: 360px; }
  .brand-name {
    font-family: "Lato", Arial, sans-serif;
    font-weight: 900;
    font-size: 72px;
    line-height: 1;
    letter-spacing: -1px;
    color: var(--brand-blue);
  }
  .brand-tagline {
    margin-top: 6px;
    font-size: 21px;
    line-height: 1.25;
    color: var(--brand-blue);
  }
  .brand-services {
    margin-top: 6px;
    font-size: 18px;
    line-height: 1.25;
    font-weight: 700;
    color: var(--brand-orange);
  }
  .contact-block { position: absolute; left: 438px; top: 118px; }
  .person-name {
    font-family: "Montserrat", Arial, sans-serif;
    font-weight: 800;
    font-size: 34px;
    letter-spacing: 0.5px;
    line-height: 1;
  }
  .person-name .first { color: var(--brand-orange); }
  .person-name .last { color: var(--brand-blue); }
  .person-title {
    margin-top: 6px;
    font-size: 22px;
    color: var(--ink-grey);
    letter-spacing: 0.5px;
  }
  .title-rule {
    width: 112px;
    height: 2px;
    margin: 12px 0 18px;
    background: var(--brand-orange);
  }
  .contact-list { list-style: none; }
  .contact-item {
    display: flex;
    align-items: center;
    gap: 14px;
    height: 44px;
    font-size: 23px;
    color: var(--ink-grey);
    letter-spacing: 0.3px;
  }
  .contact-icon { width: 32px; height: 32px; flex: none; }
  .band { position: absolute; bottom: 46px; height: 10px; }
  .band-blue { left: 46px; width: 356px; background: var(--brand-blue); }
  .band-orange { left: 410px; width: 304px; background: var(--brand-orange); bottom: 30px; }
  /* Back side */
  .card-back { top: 556px; background: var(--brand-blue); }
  .mark-frame {
    position: absolute;
    left: 270px;
    top: 80px;
    width: 220px;
    height: 220px;
    border: 2px solid var(--paper);
    display: flex;
    align-items: center;
    justify-content: center;
  }
  .mark-name {
    font-weight: 900;
    font-size: 40px;
    color: var(--paper);
    letter-spacing: -0.5px;
  }
  .back-url {
    position: absolute;
    left: 0;
    right: 0;
    top: 312px;
    text-align: center;
    font-weight: 700;
    font-size: 26px;
    color: var(--paper);
  }
  .back-services {
    position: absolute;
    left: 0;
    right: 0;
    top: 354px;
    text-align: center;
    font-size: 18px;
    letter-spacing: 0.5px;
    color: var(--paper);
  }
</style>
</head>
<body>
  <section class="card card-front">
    <div class="brand-lockup">
      <div class="brand-name">Vextorial</div>
      <div class="brand-tagline">developer of custom applications</div>
      <div class="brand-services">Bitcoin education &amp; payment integration</div>
    </div>

    <div class="contact-block">
      <h1 class="person-name"><span class="first">DALE</span> <span class="last">PARKER</span></h1>
      <p class="person-title">Software Developer</p>
      <div class="title-rule"></div>
      <ul class="contact-list">
        <li class="contact-item">
          <svg class="contact-icon" viewBox="0 0 32 32" aria-hidden="true">
            <rect width="32" height="32" rx="3" fill="var(--brand-blue)"/>
            <path d="M10 7c1-1 2.5-1 3 0l2 4c.4.8 0 1.6-.7 2l-1.3.8c.8 2.4 2.6 4.4 5 5.4l.9-1.3c.5-.7 1.3-.9 2-.5l3.7 2.1c.9.5.9 2 0 2.9l-1.6 1.6c-1.4 1.4-4.4 1-7.6-1.4S9 16.4 8.4 13C7.9 10.4 8.6 8.4 10 7z" fill="#fff"/>
          </svg>
          <span>(888) 555-VXTRL</span>
        </li>
        <li class="contact-item">
          <svg class="contact-icon" viewBox="0 0 32 32" aria-hidden="true">
            <rect width="32" height="32" rx="3" fill="var(--brand-blue)"/>
            <rect x="6" y="9" width="20" height="14" fill="none" stroke="#fff" stroke-width="2"/>
            <path d="M6 9l10 8 10-8M6 23l7.5-7M26 23l-7.5-7" fill="none" stroke="#fff" stroke-width="1.6"/>
          </svg>
          <span>dale@vextorial.com</span>
        </li>
        <li class="contact-item">
          <svg class="contact-icon" viewBox="0 0 32 32" aria-hidden="true">
            <rect width="32" height="32" rx="3" fill="var(--brand-blue)"/>
            <path d="M11 6v18l4.5-4.5 3 6.5 3-1.4-3-6.4H25z" fill="#fff"/>
          </svg>
          <span>vextorial.com</span>
        </li>
      </ul>
    </div>

    <div class="band band-blue"></div>
    <div class="band band-orange"></div>
  </section>

  <section class="card card-back">
    <div class="mark-frame">
      <span class="mark-name">Vextorial</span>
    </div>
    <p class="back-url">vextorial.com</p>
    <p class="back-services">Custom software · Bitcoin services</p>
  </section>
</body>
</html>
```